Geschäftspapiere für Jobwebseite
Zielgruppe
Hier finden sie alle Informationen zu unserem Unternehmen:
https://www.sauberwerk-stelle.com
Aufgabenstellung
Gerne von den Farben angelehnt an die Website ein modernes Briefpapier gestalten.

```html
<!DOCTYPE html>
<html lang="de">
<head>
<meta charset="utf-8">
<title>Briefpapier Sauberwerk-Stelle</title>
<link rel="stylesheet" href="https://fonts.googleapis.com/css2?family=Noto+Sans:wght@400;700&display=swap">
<style>
  :root {
    --backdrop: #e6e6e3;
    --paper: #ffffff;
    --ink: #333333;
    --ink-soft: #555555;
    --brand-green: #1e8c3a;
    --signature-tone: #e6e8f3;
  }
  * { box-sizing: border-box; margin: 0; padding: 0; }
  html, body { width: 1200px; height: 798px; overflow: hidden; }
  body {
    background: var(--backdrop);
    font-family: "Noto Sans", Verdana, sans-serif;
    color: var(--ink);
  }
  .letter {
    position: absolute;
    left: 331px; top: 19px;
    width: 537px; height: 760px;
    background: var(--paper);
    box-shadow: 0 2px 10px rgba(0,0,0,.12);
  }
  .letter > * { position: absolute; }

  .brand { left: 65px; top: 30px; display: flex; align-items: center; gap: 6px; }
  .brand-name { font-weight: 700; font-size: 12.5px; color: var(--ink); letter-spacing: .2px; }
  .brand-dot { width: 8px; height: 8px; border-radius: 50%; background: var(--brand-green); }

  .contact {
    left: 416px; top: 33px;
    font-size: 5px; line-height: 8.6px; color: var(--ink-soft);
  }
  .contact p + p { margin-top: 8.6px; }

  .sender-line { left: 66px; top: 137px; font-size: 5px; color: var(--ink-soft); white-space: nowrap; }
  .sender-line strong { color: var(--brand-green); font-weight: 700; }

  .recipient { left: 66px; top: 154px; font-size: 7.6px; line-height: 11.8px; }

  .fold-mark { left: 4px; width: 5px; height: 1px; background: var(--brand-green); }
  .fold-mark.upper { top: 230px; }
  .fold-mark.lower { top: 380px; }

  .salutation { left: 64px; top: 268px; font-size: 7.6px; }

  .body-text {
    left: 64px; top: 302px; width: 334px;
    font-size: 7.45px; line-height: 10.9px;
    hyphens: auto;
  }
  .body-text p + p { margin-top: 10.9px; }

  .closing { left: 64px; top: 616px; font-size: 7.6px; }
  .signature { left: 64px; top: 632px; width: 112px; height: 28px; }
  .signer { left: 64px; top: 659px; font-size: 7.6px; }

  .web { left: 416px; top: 728px; font-size: 5.2px; font-weight: 700; color: var(--brand-green); }
</style>
</head>
<body>
  <main class="letter">
    <div class="brand">
      <span class="brand-name">SAUBERWERK-STELLE</span>
      <span class="brand-dot"></span>
    </div>

    <address class="contact" style="font-style:normal">
      <p>sauberwerk-stelle.de<br>Lindenhof 12<br>76530 Lindental</p>
      <p>M info@sauberwerk-stelle.de<br>T 07100 555 210 4</p>
      <p>Inhaber: Herr Jonas Feldner<br>Sitz Lindental<br>Amtsgericht xxx<br>HRB xxxx</p>
    </address>

    <p class="sender-line"><strong>SAUBERWERK-STELLE.DE</strong> | Lindenhof 12 | 76530 Lindental</p>

    <p class="recipient">Firma: Musterfirma<br>Herr Maximilian Mustermann<br>Musterstraße 11<br>12345 Musterstadt</p>

    <span class="fold-mark upper"></span>
    <span class="fold-mark lower"></span>

    <p class="salutation">Sehr geehrter Herr Mustermann,</p>

    <div class="body-text">
      <p>Ferem sit, omniendaecte doluptature mo cuptatio. Ebitati ssumqui coria poreici destrum, vidusap elibus qui ipideli tatecabo. Et remporporio di quo ommolup taessit, ius non esequibus et volupiditio optatur ereicat laut et et quae ium int ma sum cori omnimin recus, ent molupti orrores truptassin eos a cor sa sus dolupta sitist laut que plignat.<br>Axim exeribus. Pudit arum ium ipiet in ni od mos ent liciam quunt aborporem verferr uptasim ra de int quunt a inimin et il mi, eaque volo bla volo bea qui ius, sum volo Ibus, acepernatem aut explabo rporupta pa qui consediam atus.</p>
      <p>Aximporporum et dolore conecerferia venimet verae sum nobist asintorest, eosant alique volut qui te nullo eum que velitatatis iumque mint ut volupta tquiatemodi dolless itature, et laccuptae pa invelis sequunt, velique abo. Obis sus et officipsamus premquidi blabo. Dollore rnatend untiatu reperion consequam faccaborit faciates sitatenet harunt invenim di sumque.</p>
      <p>Pore oditam identitiis dit estrunt officta tecust pro maionsequis del mos aut quiatur? Icillab ipsapie nihilluptas mo et que sitatiis dolupta quament laborro cuptae. Namus, utendunt.Pictat. Otae nimet faccatur? Erumqui at occum ratquia nos viti con reiunt volorro ommodit, nusam ratiasr itatet pa quistionsed explitem. Nam inis essinve litatib usdandit miliaspedi aces utatem facia volesci alit evel iuntis unt ab ilit autem quam archilluptae</p>
      <p>Sit laut qui tem rerum as reperae prorempedi neces et acculparum fugiae denetur, torernam verepti issinullenis arum re dolessi sum rerum ra di que vel minciam duntio. Aborios molutae praest, corit quiaerci sus andigente sincius si occum fugiae reperibus delicab is sunt magnam is vento to blandiscia quo dolorro vitasped evelest, suntemp oreictor a porepudaeri que conem aut mint alitam si quae volorro rerferia volorepeliti ad ma voluptat acest estrupta si voloriscid millatatae re, offictis aperor maio. Ut liquam erum eum dunt offici dolenih ilibus, id erro et volupta volectent que pla sitis exped maio. Nam sitatur sit qui comnima ximpore consect ibeatatum aut in nulparc hilite nonsequia autemquat.</p>
    </div>

    <p class="closing">Mit freundlichen Grüßen</p>
    <svg class="signature" viewBox="0 0 112 28" role="img" aria-label="Handschriftliche Unterschrift des Absenders">
      <rect width="112" height="28" fill="var(--signature-tone)"/>
    </svg>
    <p class="signer">Max Mustermann</p>

    <p class="web">www.sauberwerk-stelle.com</p>
  </main>
</body>
</html>
```